New Year's card HTML

can you produce a best new years wishes 2018 design in HTML for our website as what I would like to send by email towards my network of candidates / customers ...

It must be wow, inspiring , design, meaningfull... MMM those people care about me, or those people will help me to go the extra mile, to help me to achieve my career goals, Your best move, enhance my possibilities, bring the love back

Target Market(s)

CEo's / CMO's/ HRDirectors network of 450k

Coding

Coded - Design and coding required

Number of Pages Required

1 page

Colors

Designer to choose colors to be used in the design.

Requirements
Must have
• Logo / visual / website adress www.moravintel.com and a call to action
Should not have
• no sound as our business is confidential

```html
<!DOCTYPE html>
<html lang="en">
<head>
<meta charset="utf-8">
<title>Moravintel – Happy New Year 2018</title>
<link rel="stylesheet" href="https://fonts.googleapis.com/css2?family=Cormorant+Garamond:ital,wght@0,500;1,500&family=Cinzel:wght@400&family=Yanone+Kaffeesatz:wght@400&display=swap">
<style>
  :root {
    --header-bg: #1d1d1d;
    --night-deep: #0e1220;
    --night-mid: #1a2030;
    --spark-gold: #c9a465;
    --bokeh-teal: #4b5f60;
    --text-light: #ffffff;
    --text-soft: #e6dcc6;
    --cta-red: #d43d22;
  }
  * { margin: 0; padding: 0; box-sizing: border-box; }
  html, body {
    width: 1200px;
    height: 1090px;
    overflow: hidden;
    background: var(--night-deep);
  }
  .card {
    position: relative;
    width: 1200px;
    height: 1090px;
    overflow: hidden;
  }
  .brand-bar {
    position: absolute;
    top: 0; left: 0;
    width: 1200px;
    height: 165px;
    background: var(--header-bg);
    display: flex;
    align-items: center;
    justify-content: center;
    gap: 28px;
    z-index: 2;
  }
  .brand-dot {
    width: 26px;
    height: 26px;
    border-radius: 50%;
    background: var(--text-light);
  }
  .brand-name {
    font-family: "Cormorant Garamond", serif;
    font-weight: 500;
    font-size: 58px;
    letter-spacing: 2px;
    color: var(--text-light);
    line-height: 1;
  }
  .hero-visual {
    position: absolute;
    top: 165px; left: 0;
    width: 1200px;
    height: 925px;
    background:
      radial-gradient(ellipse 70% 35% at 50% 8%, rgba(201,164,101,0.75), rgba(201,164,101,0) 70%),
      radial-gradient(ellipse 40% 25% at 5% 20%, rgba(220,190,120,0.5), rgba(220,190,120,0) 70%),
      radial-gradient(ellipse 80% 30% at 50% 95%, rgba(75,95,96,0.8), rgba(75,95,96,0) 75%),
      linear-gradient(180deg, #3a2f22 0%, var(--night-mid) 35%, var(--night-deep) 60%, #1f2a2e 100%);
  }
  .greeting {
    position: absolute;
    top: 405px; left: 0;
    width: 1200px;
    text-align: center;
    color: var(--text-light);
    font-family: "Cinzel", serif;
    font-weight: 400;
    z-index: 2;
  }
  .greeting-line {
    display: block;
    font-size: 92px;
    line-height: 110px;
    letter-spacing: -2px;
  }
  .greeting-year {
    display: block;
    margin-top: 14px;
    font-size: 84px;
    line-height: 90px;
    letter-spacing: 10px;
  }
  .cta-button {
    position: absolute;
    top: 689px;
    left: 360px;
    width: 482px;
    height: 108px;
    border-radius: 5px;
    background: var(--cta-red);
    color: var(--text-light);
    font-family: "Yanone Kaffeesatz", sans-serif;
    font-weight: 400;
    font-size: 64px;
    line-height: 108px;
    text-align: center;
    text-decoration: none;
    z-index: 2;
  }
  .wish {
    position: absolute;
    top: 836px; left: 150px;
    width: 900px;
    text-align: center;
    font-family: "Cormorant Garamond", serif;
    font-style: italic;
    font-weight: 500;
    font-size: 34px;
    line-height: 44px;
    color: var(--text-soft);
    z-index: 2;
  }
  .site-address {
    position: absolute;
    top: 1004px; left: 0;
    width: 1200px;
    text-align: center;
    font-family: "Cormorant Garamond", serif;
    font-weight: 500;
    font-size: 30px;
    letter-spacing: 3px;
    color: var(--text-light);
    text-decoration: none;
    z-index: 2;
  }
</style>
</head>
<body>
  <main class="card">
    <header class="brand-bar">
      <span class="brand-dot" aria-hidden="true"></span>
      <span class="brand-name">MORAVINTEL</span>
    </header>
    <div class="hero-visual" role="img" aria-label="Golden fireworks bursting over a dark night sky with soft blurred city lights below"></div>
    <h1 class="greeting">
      <span class="greeting-line">HAPPY NEW YEAR</span>
      <span class="greeting-year">2018</span>
    </h1>
    <a class="cta-button" href="https://www.moravintel.com">VIEW MY SITE</a>
    <p class="wish">Thank you for going the extra mile with us.<br>May 2018 bring your best move yet.</p>
    <a class="site-address" href="https://www.moravintel.com">www.moravintel.com</a>
  </main>
</body>
</html>
```